Stationery Design Project

We need a stationery design for our Norwegian trucking company. We have existed for about 15 years and our 12 drivers uses relatively new vehicles to transport goods around in northern Norway. Long distance routes with fresh fish og food transport is our main operations.

We have already made alogo that's printed on our trucks. The logo and a picture of our trucks is attached. I think the logo i crappy, but since its already in use, changing it is not an option in this round. Still using a better colour scheme in the overall stationery and more interesting fonts is possible (altso in the logo).

Company details:
Name: Kjelvraket AS
Organisation nr 873 615 309
Post adress: 8642 Raudvik

I like minimalism and simplicity. I am avalibly for questions in normal GMT working hours either here or on mail: ivar@fjordlast.no

Reason: Hi. Im extending the deadline because I needed some time to find a vector file of our logo. Sorry for the inconvenience

Hi, and thanks for all your interest in the project. Some updates:

-          I have decided to commit to using one of the designs. Some designer will get the payment.

-          I have extended the deadline with 24 hours since I needed some time to find our firms vector logo (a slow Swedish man was holding me up)

-          We will not choose a design before the deadline. No need to rush.

-          We have received a lot of great design and think there is a need to specified the product we want to make:

o   Business Card for all our employers. I just need the design and will duplicate with the correct numbers and name myself. The information on should be: Logo, employer’s name, Phone number, email, website, Postal number and address. Use this as a template: logo, Leif Brattvoll, 47382066, Leif@fjordlast.no,, fjordlast.no, 8642 Raudvik. The order and placement of the information is your creative decision.

o   Stickers to put on the goods we travel. On the sticker the should be the following information: Logo, phone number, Tekst and link: Fraktæ av Kjelvraket. Ke du syns? Fjordlast.no/tilbakemelding (this means: Handled by Kjelvraket. What do you think Fjordlast.no/feedback -à the link will be a feedback form). The placement the information and size is your creative decision with some stings: we have been thinking of using Drukko for printing and see that a size about 6x6 cm, 8x5 or something like that. (with 3000 copies our budget is 200 punds). Any suggestions of other suppliers are welcome. Drukko price calculator http://www.drukkolabelhouse.co.uk/digital-litho-printing/printing-labels-tags/stickers/

o   Letterhead with logo, address, phone number and organizational number.

o   Envelopes with logo,address, phone number and organizational number.

Have a nice day.

 

 

• Using the blue colour in the logo and using a similar graphic approch.

```html
<!DOCTYPE html>
<html lang="no">
<head>
<meta charset="utf-8">
<title>Kjelvraket – visittkort</title>
<link rel="stylesheet" href="https://fonts.googleapis.com/css2?family=Source+Sans+3:wght@400;700&display=swap">
<style>
  :root {
    --blue-deep: #1b4e9b;
    --blue-mid: #0b72ba;
    --ink: #2b2b2b;
    --rule: #b9b9b9;
    --paper: #ffffff;
    --backdrop: #e4e6e8;
  }
  * { margin: 0; padding: 0; box-sizing: border-box; }
  html, body { width: 1200px; height: 1075px; overflow: hidden; }
  body {
    background: var(--backdrop);
    font-family: "Source Sans 3", Arial, sans-serif;
    position: relative;
  }
  .card {
    position: absolute;
    width: 767px;
    height: 438px;
    background: var(--paper);
    box-shadow: 0 2px 8px rgba(0,0,0,0.18);
    overflow: hidden;
  }
  .card--front { left: 94px; top: 70px; }
  .card--back { left: 316px; top: 561px; }
  .wordmark {
    position: absolute;
    left: 118px;
    top: 100px;
    font-weight: 700;
    font-size: 112px;
    line-height: 1;
    letter-spacing: -1px;
    color: var(--blue-mid);
  }
  .contact {
    position: absolute;
    top: 284px;
    font-size: 21px;
    line-height: 31px;
    color: var(--ink);
  }
  .contact--left { right: 412px; text-align: right; }
  .contact--right { left: 396px; }
  .contact-divider {
    position: absolute;
    left: 375px;
    top: 290px;
    width: 1px;
    height: 92px;
    background: var(--rule);
  }
  .person-name {
    font-weight: 700;
    font-size: 24px;
    color: var(--blue-deep);
  }
  .org-label { color: var(--blue-mid); }
  .line { display: flex; align-items: center; gap: 7px; }
  .contact--left .line { justify-content: flex-end; }
  .icon { width: 15px; height: 15px; fill: var(--blue-deep); flex: none; }
  .back-url {
    position: absolute;
    left: 0; right: 0;
    top: 278px;
    text-align: center;
    font-size: 26px;
    letter-spacing: 0.22em;
    color: var(--ink);
  }
</style>
</head>
<body>

<section class="card card--front">
  <div class="wordmark">Kjelvraket</div>

  <div class="contact contact--left">
    <div class="person-name">Leif Brattvoll</div>
    <div class="line">
      <svg class="icon" viewBox="0 0 16 16"><path d="M1,15 V7 L8,2 L15,7 V15 H10 V10 H6 V15 Z"/></svg>
      <span>8642 Raudvik</span>
    </div>
    <div class="line">
      <svg class="icon" viewBox="0 0 16 16"><path d="M4,1 L7,4 L5,6 C6,9 7,10 10,11 L12,9 L15,12 L12,15 C6,14 2,10 1,4 Z"/></svg>
      <span>47382066</span>
    </div>
  </div>

  <div class="contact-divider"></div>

  <div class="contact contact--right">
    <div><span class="org-label">Org nr</span> 873 615 309</div>
    <div class="line">
      <svg class="icon" viewBox="0 0 16 16"><path d="M1,4 H15 V13 H1 Z M1,4 L8,9 L15,4" stroke="#fff" stroke-width="1.2"/></svg>
      <span>Leif@fjordlast.no</span>
    </div>
    <div class="line">
      <svg class="icon" viewBox="0 0 16 16"><circle cx="8" cy="8" r="7"/><path d="M1,8 H15 M8,1 C4,5 4,11 8,15 M8,1 C12,5 12,11 8,15" stroke="#fff" stroke-width="1.1" fill="none"/></svg>
      <span>www.fjordlast.no</span>
    </div>
  </div>
</section>

<section class="card card--back">
  <div class="wordmark">Kjelvraket</div>
  <div class="back-url">www.fjordlast.no</div>
</section>

</body>
</html>
```